Corporate Travel Technology Company needs new Business Card design

We need a new business card design to reflect our re-branded company. Our company is called Tolven (pronounced tolvenn) and we provide Business Intelligence and Smart Corporate Trip Planning solutions for the corporate travel industry. Our multinational customers use our solutions to manage large travel budgets and frequent travellers, as well as to save money and reduce risk. We'd like to see designs that use the blue and green palette as well as our corporate logo (attached below). The design should communicate innovation, insight, forward thinking, contemporary, trusted.

Target Market(s)

Large multinational corporates and Travel Agencies.

Industry/Entity Type

Business

Contact Information for Business Card

Rosalind Mercer
Chief Executive
Tolven
Phone number - +61 (0)2 8134 2907
Email address - rosalind.mercer@tolven-example.com
Mobile number - +61 (0)438 516 702
www.tolven-example.com

Font styles to use
Other font styles liked:
• Please use font as close to corporate logo as possible

Colors
0255a3
0393ce
00a990
33b8a4
33a6d7
3176b5

Requirements
Must have
• Please include the words;
• Smart Corporate Trip Planning
• Driving Clearer Travel Spend Decisions
• Use corporate logo - although icon can be stylised if needed

```html
<!DOCTYPE html>
<html lang="en">
<head>
<meta charset="utf-8">
<title>Tolven — Business Card</title>
<link href="https://fonts.googleapis.com/css2?family=Open+Sans:wght@400;600;700&display=swap" rel="stylesheet">
<style>
  :root {
    --bg: #e6e7e8;
    --card: #ffffff;
    --slate: #3b5255;
    --blue: #29a9e1;
    --white: #ffffff;
  }
  * { box-sizing: border-box; margin: 0; padding: 0; }
  html, body {
    width: 1200px; height: 900px; overflow: hidden;
    background: var(--bg);
    font-family: "Open Sans", Arial, sans-serif;
  }
  .canvas { position: relative; width: 1200px; height: 900px; }
  .card {
    position: absolute; left: 280px;
    width: 640px; height: 366px;
    background: var(--card);
    overflow: hidden;
    box-shadow: 0 2px 8px rgba(0,0,0,0.12);
  }
  .card--front { top: 60px; }
  .card--back { top: 474px; }

  /* Company name */
  .company-name {
    position: absolute;
    color: var(--slate); font-weight: 600; letter-spacing: -1px;
    line-height: 1; white-space: nowrap;
  }
  .card--front .company-name {
    left: 0; right: 0; top: 86px; text-align: center; font-size: 84px;
  }

  .taglines {
    position: absolute; left: 0; right: 0; top: 224px;
    text-align: center; font-weight: 700;
  }
  .taglines__primary { color: var(--blue); font-size: 21px; }
  .taglines__secondary { color: var(--slate); font-size: 23px; margin-top: 2px; }

  /* Back */
  .back-art { position: absolute; inset: 0; }
  .contact {
    position: absolute; left: 30px; top: 150px;
    list-style: none; color: var(--white); font-size: 15.5px;
  }
  .contact li { display: flex; align-items: center; gap: 12px; height: 22px; white-space: nowrap; }
  .contact svg { width: 13px; height: 13px; flex: none; }
  .person {
    position: absolute; left: 400px; top: 104px; width: 184px; text-align: center;
  }
  .person__name { color: var(--slate); font-weight: 700; font-size: 19px; }
  .person__role { color: var(--blue); font-size: 15.5px; }
  .card--back .company-name {
    left: 376px; top: 252px; font-size: 60px;
  }
</style>
</head>
<body>
<main class="canvas">

  <section class="card card--front" aria-label="Card front">
    <p class="company-name">Tolven</p>
    <div class="taglines">
      <p class="taglines__primary">Smart Corporate Trip Planning</p>
      <p class="taglines__secondary">Driving Clearer Travel Spend Decisions</p>
    </div>
  </section>

  <section class="card card--back" aria-label="Card back">
    <svg class="back-art" viewBox="0 0 640 366" aria-hidden="true">
      <circle cx="120" cy="280" r="240" fill="var(--blue)"/>
      <path d="M-10 62 Q 200 10 345 118" fill="none" stroke="var(--white)" stroke-width="16"/>
      <path d="M-10 62 Q 200 10 340 114" fill="none" stroke="var(--slate)" stroke-width="8"/>
      <polygon points="328,92 362,130 318,124" fill="var(--slate)"/>
    </svg>

    <ul class="contact">
      <li><svg viewBox="0 0 16 16"><path fill="#fff" d="M2 4c0-2 3-3 6-3s6 1 6 3v2h-3V4H5v2H2zM4 7h8l2 7H2z"/></svg>+61 (0)2 8134 2907</li>
      <li><svg viewBox="0 0 16 16"><rect x="4" y="1" width="8" height="14" rx="1.5" fill="#fff"/><rect x="5.5" y="3" width="5" height="8" fill="var(--blue)"/></svg>+61 (0)438 516 702</li>
      <li><svg viewBox="0 0 16 16"><rect x="1" y="3" width="14" height="10" fill="#fff"/><path d="M1 3l7 6 7-6" fill="none" stroke="var(--blue)" stroke-width="1.5"/></svg>rosalind.mercer@tolven-example.com</li>
      <li><svg viewBox="0 0 16 16"><path d="M7 9l2-2M6 7L4 9a2 2 0 0 0 3 3l2-2M10 9l2-2a2 2 0 0 0-3-3L7 6" fill="none" stroke="#fff" stroke-width="1.8" stroke-linecap="round"/></svg>www.tolven-example.com</li>
    </ul>

    <div class="person">
      <p class="person__name">Rosalind Mercer</p>
      <p class="person__role">Chief Executive</p>
    </div>

    <p class="company-name">Tolven</p>
  </section>

</main>
</body>
</html>
```